Corvanth Veylor - Advanced Skincare and undetectable Makeup for Men

We are in need of a professional webpage for our company Corvanth Veylor. We help every man feel his best by looking his best. Inspired by the myth of Corvanth, we offer makeup and skincare products along with education upon their use. Our mission is to celebrate masculinity in all of its forms, regardless of age, race, sexual orientation, or assigned gender at birth.

The webpage would serve as our online store, as a place where our clients can learn about our brand, view our "How-to" video tutorials, and get product information. An online blog will also be hosted in order to keep clients up to date with news, updates, media mentions, etc.

The color schemes that we use are mostly Black and Gold, with Red accents. please keep in mind that this is a men's cosmetics line, and therefore should read powerful, sexy, confident and bold - all with a high end look and feel.

Think along the lines of brands like Lem Brisko, QDV, Belluti, etc.

our logo is included in the files attached. images and copy will be added in at a later time; hence, general images that fit the feel and filler text is encouraged.

The products to be sold include:
a face cleanser in a pump dispenser bottle (1 size)
a mask in a round jar container (1 size)
a moisturizer in a pump container 1 size)
a concealer in a click pen with a brush applicator (3 shades)
a liquid liner pen (4 shades)
a contouring palette (2 shade options)
a setting spray (single option)

Target Market(s)

Millennial Men

Industry/Entity Type

Beauty

Number of Pages Required

5+ page

Font styles to use
Serif

Colors
ec1f27
000000
faa54b

Requirements
Must have
• ur essential requirements are:
• 1) a stunning and engaging landing page that truly captures the ideals of sexuality, boldness and confidence.
• 2) an interactive and engaging online store that is easy to update / add product / information to.
• 3) Product pages supporting various toggling images of the product, a shade selection option, ingredient information, usage instructions, pricing, and a link to a "how to video" unique to each individual product.
• 4) dedicated space where all of the tutorials can be organized together
• 5) an organized Blog section, that would include a segment for a Q&A section for us to update as the brand grows, ongoing contests (that would be easily hidden if there are no contests running at the moment) as well as general news and updates segment.
• 6) an "about us" page, where our customers are able to learn about our story, inspirations, humanitarian efforts and philosophies in product contents and purity.
• 7) a contact us page, which would include social media links, contact email and telephone number as well as physical address to be updated upon launch.
• 8) discrete privacy policy, terms of use, and return policy links available at the bottom of every page
Nice to have
• 1) A posting forum where clients could post their looks using our products, or maybe a live stream of our Pictoval account.
• 2) a member sign in page so that we can collect and store customer information for faster check out, keep track of purchases attached to their email address (future loyalty program plans) and maintain an email database for email notifications and the such.

```html
<!DOCTYPE html>
<html lang="en">
<head>
<meta charset="utf-8">
<title>Corvanth Veylor</title>
<link href="https://fonts.googleapis.com/css2?family=Noto+Serif:ital,wght@0,400;0,700;1,400&family=Arimo:wght@400;700&display=swap" rel="stylesheet">
<style>
:root{
  --black:#000;
  --ink:#222;
  --text:#444;
  --gold:#c8952a;
  --gold-btn:#c9992f;
  --red:#ec1f27;
  --gray-bg:#ececec;
  --white:#fff;
}
*{margin:0;padding:0;box-sizing:border-box}
html,body{width:1200px;height:3352px;overflow:hidden;background:var(--white)}
body{position:relative;font-family:"Arimo",Arial,sans-serif;color:var(--text)}
.serif{font-family:"Noto Serif",Georgia,serif}
section,header,footer{position:absolute;left:0;width:1200px}
.abs{position:absolute}

/* header */
.site-header{top:0;height:123px;background:var(--black);border-bottom:3px solid var(--gold)}
.brand{left:79px;top:24px;width:200px;text-align:center}
.brand-mark{width:38px;height:38px;border:2px solid var(--gold);margin:0 auto 10px}
.brand-name{font-family:"Noto Serif",Georgia,serif;color:var(--gold);font-size:12.5px;letter-spacing:2px;white-space:nowrap}
.utility{top:26px;left:405px;display:flex;align-items:center;font-size:11px;color:#bbb;letter-spacing:1px}
.utility .u{padding:0 20px;border-right:1px solid #555;line-height:12px}
.utility .u:nth-child(4){border-right:1px solid #555}
.search{margin-left:12px;width:218px;border-bottom:1px solid #666;padding:0 0 6px 6px;display:flex;justify-content:space-between;align-items:center}
.nav-item{top:85px;width:120px;margin-left:-60px;text-align:center;font-family:"Noto Serif",Georgia,serif;font-size:12px;color:#ddd;white-space:nowrap}

/* hero */
.hero{top:123px;height:554px;overflow:hidden;background:linear-gradient(90deg,#cdbba4 0%,#e2d6c7 38%,#dcd7d1 62%,#cbc8c4 100%)}
.hero-photo{left:0;top:0;width:620px;height:554px;
  background:
    radial-gradient(ellipse 170px 230px at 330px 250px,#efd5c2 0%,#e6c4ac 55%,rgba(230,196,172,0) 100%),
    radial-gradient(ellipse 220px 160px at 330px 60px,#5a3f2e 0%,rgba(90,63,46,0) 100%),
    linear-gradient(90deg,#c3b09a 0%,#d8c7b5 70%,rgba(221,210,198,0) 100%)}
.hero-title{left:620px;top:180px;width:484px;text-align:center;font-size:46px;color:var(--gold);letter-spacing:1px;white-space:nowrap;font-weight:400}
.hero-copy{left:620px;top:250px;width:484px;text-align:center;font-style:italic;font-size:15px;line-height:30px;color:#3a2a1a}
.btn{display:block;background:var(--gold-btn);color:var(--white);text-align:center;border-radius:26px;font-family:"Noto Serif",Georgia,serif;font-size:14px}
.hero-btn{left:773px;top:335px;width:179px;height:50px;line-height:50px}
.arrow-btn{top:260px;width:34px;height:34px;border:2px solid rgba(255,255,255,.9);border-radius:50%}

/* about */
.about{top:677px;height:575px;background:var(--gray-bg)}
.about-card{left:139px;top:76px;width:923px;height:425px;background:var(--white);box-shadow:0 0 4px rgba(0,0,0,.1)}
.about-olive{left:686px;top:0;width:237px;height:425px;background:linear-gradient(150deg,#86802f,#5e5a1c 60%,#4c4916)}
.about-frame{left:534px;top:29px;width:322px;height:369px;background:var(--white);padding:9px;box-shadow:0 0 6px rgba(0,0,0,.15)}
.ph{width:100%;height:100%}
.section-title{font-family:"Noto Serif",Georgia,serif;color:var(--gold);font-size:31px;letter-spacing:1px;font-weight:400}
.about-title{left:43px;top:74px}
.about-text{left:43px;top:136px;width:433px;font-size:11.5px;line-height:25px;color:#555}
.about-text p+p{margin-top:18px}

.center{left:0;width:1200px;text-align:center}
.sub{font-size:12px;color:#555}

/* products */
.products{top:1252px;height:574px;background:var(--white)}
.product{top:152px;width:334px;height:270px;overflow:hidden}
.product-label{position:absolute;left:0;bottom:0;width:100%;height:48px;line-height:48px;background:rgba(0,0,0,.55);color:var(--white);text-align:center;font-family:"Noto Serif",Georgia,serif;font-size:14px;letter-spacing:1px}
.products-btn{left:505px;top:469px;width:190px;height:50px;line-height:50px;font-size:13px}

/* video */
.video{top:1826px;height:620px}
.video-band{left:0;top:0;width:1200px;height:333px;background:linear-gradient(160deg,#cfa23a,#bf8f2b)}
.video-title{top:42px;color:var(--white);font-size:32px;font-weight:400}
.video-text{left:245px;top:98px;width:710px;text-align:center;color:#fff3dd;font-size:11.5px;line-height:23px}
.video-frame{left:197px;top:179px;width:807px;height:411px;overflow:hidden}
.play{left:363px;top:165px;width:80px;height:80px;border-radius:50%;background:var(--red);box-shadow:0 2px 10px rgba(0,0,0,.3)}

/* blog */
.blog{top:2446px;height:567px}
.post{top:117px;width:328px}
.post-img{height:222px}
.post-title{margin-top:24px;font-family:"Noto Serif",Georgia,serif;font-size:15px;color:#333;letter-spacing:.5px;font-weight:400}
.post-date{margin-top:10px;color:var(--gold);font-family:"Noto Serif",Georgia,serif;font-size:14px;display:flex;align-items:center;gap:8px}
.post-text{margin-top:10px;font-size:11.5px;line-height:25px;color:#555}

/* footer */
.site-footer{top:3013px;height:339px;background:var(--black);color:#ddd}
.f-col{top:47px}
.f-head{font-weight:700;font-size:14.5px;color:var(--white);letter-spacing:.5px;margin-bottom:20px;white-space:nowrap}
.f-list{list-style:none;font-size:12px;line-height:25.5px;white-space:nowrap}
.f-list li::before{content:"";display:inline-block;border-left:5px solid #ddd;border-top:4px solid transparent;border-bottom:4px solid transparent;margin-right:18px;vertical-align:1px}
.cards{display:flex;gap:5px}
.card{width:38px;height:24px;background:#e8e8e8;color:#111;font-size:8px;line-height:24px;text-align:center}
.socials{display:flex;gap:5px;margin-top:52px}
.social{width:38px;height:38px;border:2px solid #ddd;border-radius:50%;font-size:7.5px;line-height:34px;text-align:center;color:#ddd}
.contact-row{display:flex;align-items:flex-start;gap:16px;font-size:12px;line-height:15px;margin-bottom:14px;white-space:nowrap}
.contact-row svg{flex:none;margin-top:1px}
.f-rule{left:0;top:264px;width:1200px;height:1px;background:#222}
.copyright{top:289px;font-size:12px;color:#ddd}
</style>
</head>
<body>

<header class="site-header">
  <div class="abs brand">
    <div class="brand-mark"></div>
    <div class="brand-name">CORVANTH VEYLOR</div>
  </div>
  <div class="abs utility">
    <span class="u">&#128274; LOGIN</span><span class="u">&#128100; REGISTER</span><span class="u">&#8644; COMPARE</span><span class="u">&#128722; CART</span>
    <div class="search"><span>SEARCH</span>
      <svg width="13" height="13" viewBox="0 0 13 13"><circle cx="5.5" cy="5.5" r="4.2" fill="none" stroke="#bbb" stroke-width="1.6"/><line x1="8.6" y1="8.6" x2="12" y2="12" stroke="#bbb" stroke-width="1.8"/></svg>
    </div>
  </div>
  <nav>
    <a class="abs nav-item" style="left:409px">HOME</a>
    <a class="abs nav-item" style="left:514px">ABOUT US</a>
    <a class="abs nav-item" style="left:630px">SERVICES</a>
    <a class="abs nav-item" style="left:747px">PRODUCTS</a>
    <a class="abs nav-item" style="left:855px">NEWS</a>
    <a class="abs nav-item" style="left:957px">GALLERY</a>
    <a class="abs nav-item" style="left:1078px">CONTACT US</a>
  </nav>
</header>

<section class="hero">
  <div class="abs hero-photo" role="img" aria-label="Portrait of a model applying cotton pads to the face"></div>
  <div class="abs arrow-btn" style="left:42px"><svg width="30" height="30" viewBox="0 0 30 30"><polyline points="17,9 11,15 17,21" fill="none" stroke="#fff" stroke-width="2"/></svg></div>
  <div class="abs arrow-btn" style="left:1120px"><svg width="30" height="30" viewBox="0 0 30 30"><polyline points="13,9 19,15 13,21" fill="none" stroke="#fff" stroke-width="2"/></svg></div>
  <h1 class="abs hero-title serif">CORVANTH VEYLOR</h1>
  <p class="abs hero-copy serif">Sed ut perspiciatis unde omnis iste natus error sit voluptatem doloremque laudantium vitae dicta sunt explicabo.</p>
  <a class="abs btn hero-btn">READ MORE</a>
</section>

<section class="about">
  <div class="abs about-card">
    <div class="abs about-olive"></div>
    <h2 class="abs section-title about-title">ABOUT US</h2>
    <div class="abs about-text">
      <p>Sed ut perspiciatis unde omnis iste natus error sit voluptatem accusantium doloremque laudantium, totam rem aperiam, eaque ipsa quae ab illo inventore veritatis et quasi architecto beatae vitae dicta sunt explicabo. Nemo enim ipsam voluptatem quia volup tas sit aspernatur aut odit aut fugit, sed quia consequuntur magni dolores eos qui ratione voluptatem sequi nesciunt.</p>
      <p>Sed ut perspiciatis unde omnis iste natus error sit voluptatem accusantium doloremque laudantium, totam rem aperiam, eaque ipsa quae ab illo inventore veritatis et quasi architecto beatae vitae dicta sunt explicabo.</p>
    </div>
    <div class="abs about-frame">
      <div class="ph" role="img" aria-label="Close-up portrait showing a facial contour lift treatment" style="background:radial-gradient(ellipse 110px 150px at 180px 180px,#edcdb6 0%,#dcb196 60%,rgba(220,177,150,0) 100%),radial-gradient(ellipse 160px 90px at 170px 30px,#5b4030 0%,rgba(91,64,48,0) 100%),linear-gradient(135deg,#9fabb1,#c9c2bb 55%,#c7a790)"></div>
    </div>
  </div>
</section>

<section class="products">
  <h2 class="abs center section-title" style="top:44px">OUR PRODUCTS</h2>
  <p class="abs center sub" style="top:92px">Sed ut perspiciatis unde omnis iste natus error sit voluptatem accusantium doloremque laudantium</p>
  <div class="abs product" style="left:85px">
    <div class="ph" role="img" aria-label="Hand dipping into a round jar of face mask" style="background:radial-gradient(ellipse 120px 60px at 175px 190px,#1c1a1c 0%,#2f2b2d 60%,rgba(47,43,45,0) 100%),radial-gradient(ellipse 110px 90px at 180px 90px,#e0c4b0 0%,rgba(224,196,176,0) 100%),linear-gradient(135deg,#cfc4bb,#8b817a 60%,#3a3434)"></div>
    <div class="product-label">MASK</div>
  </div>
  <div class="abs product" style="left:434px">
    <div class="ph" role="img" aria-label="Model using setting spray at a lit vanity mirror" style="background:radial-gradient(circle 14px at 60px 40px,#fff6d8,rgba(255,246,216,0)),radial-gradient(circle 14px at 130px 40px,#fff6d8,rgba(255,246,216,0)),radial-gradient(circle 14px at 200px 40px,#fff6d8,rgba(255,246,216,0)),radial-gradient(ellipse 90px 140px at 270px 140px,#5a3624 0%,rgba(90,54,36,0) 100%),linear-gradient(135deg,#8a5e45,#c99a72 50%,#dec7b0)"></div>
    <div class="product-label">SETTING SPRAY</div>
  </div>
  <div class="abs product" style="left:780px">
    <div class="ph" role="img" aria-label="Contouring palette with sponge and foundation bottle" style="background:radial-gradient(ellipse 45px 55px at 220px 60px,#e99f77 0%,rgba(233,159,119,0) 100%),radial-gradient(ellipse 40px 70px at 60px 70px,#151515 0%,rgba(21,21,21,0) 100%),radial-gradient(ellipse 120px 55px at 230px 170px,#c7916f 0%,rgba(199,145,111,0) 100%),linear-gradient(135deg,#56626b,#8e999e 55%,#b89b87)"></div>
    <div class="product-label">CONTOURING PALETTE</div>
  </div>
  <a class="abs btn products-btn">VIEW ALL PRODUCTS</a>
</section>

<section class="video">
  <div class="abs video-band"></div>
  <h2 class="abs center video-title serif">VIDEO TUTORIALS</h2>
  <p class="abs video-text">Sed ut perspiciatis unde omnis iste natus error sit voluptatem accusantium doloremque laudantium, totam rem aperiam, eaque ipsa quae ab illo inventore veritatis et quasi architecto beatae vitae dicta sunt explicabo.</p>
  <div class="abs video-frame">
    <div class="ph" role="img" aria-label="Video still of a facial cleansing treatment with cotton pads" style="background:radial-gradient(ellipse 170px 70px at 405px 40px,#4f7fa6 0%,rgba(79,127,166,0) 100%),radial-gradient(ellipse 150px 170px at 405px 200px,#eed3c1 0%,#e0bea6 60%,rgba(224,190,166,0) 100%),linear-gradient(180deg,#c4c8ce,#ddd0c3 50%,#cbb39f)"></div>
    <div class="abs play"><svg width="80" height="80" viewBox="0 0 80 80"><polygon points="32,25 56,40 32,55" fill="#fff"/></svg></div>
  </div>
</section>

<section class="blog">
  <h2 class="abs center section-title" style="top:24px">LATEST BLOG</h2>
  <p class="abs center sub" style="top:72px">Sed ut perspiciatis unde omnis iste natus error sit voluptatem accusantium doloremque laudantium</p>

  <article class="abs post" style="left:85px">
    <div class="post-img" role="img" aria-label="Beauty portrait on a peach background" style="background:radial-gradient(ellipse 70px 90px at 90px 90px,#e8c0a6 0%,rgba(232,192,166,0) 100%),radial-gradient(ellipse 80px 70px at 80px 20px,#4a3125 0%,rgba(74,49,37,0) 100%),linear-gradient(135deg,#f0c6b0,#f7ddcf)"></div>
    <h3 class="post-title">SED UT PERSPICIATIS UNDE</h3>
    <div class="post-date"><svg width="14" height="14" viewBox="0 0 14 14"><rect x="1" y="2.5" width="12" height="10.5" fill="none" stroke="#c8952a" stroke-width="1.4"/><line x1="1" y1="5.5" x2="13" y2="5.5" stroke="#c8952a" stroke-width="1.4"/></svg>02 Aug 2018</div>
    <p class="post-text">Nemo enim ipsam voluptatem quia voluptas sit aspernatur aut odit aut fugit, sed quia consequuntur magni dolores eos qui ratione voluptatem sequi nesciunt.</p>
  </article>
  <article class="abs post" style="left:436px">
    <div class="post-img" role="img" aria-label="Model touching up makeup at a mirror" style="background:radial-gradient(ellipse 60px 80px at 100px 80px,#d9b29a 0%,rgba(217,178,154,0) 100%),radial-gradient(ellipse 90px 120px at 250px 100px,#1f1818 0%,rgba(31,24,24,0) 100%),linear-gradient(135deg,#e2e2e2,#a69891 55%,#4a4040)"></div>
    <h3 class="post-title">SED UT PERSPICIATIS UNDE</h3>
    <div class="post-date"><svg width="14" height="14" viewBox="0 0 14 14"><rect x="1" y="2.5" width="12" height="10.5" fill="none" stroke="#c8952a" stroke-width="1.4"/><line x1="1" y1="5.5" x2="13" y2="5.5" stroke="#c8952a" stroke-width="1.4"/></svg>02 Aug 2018</div>
    <p class="post-text">Nemo enim ipsam voluptatem quia voluptas sit aspernatur aut odit aut fugit, sed quia consequuntur magni dolores eos qui ratione voluptatem sequi nesciunt.</p>
  </article>
  <article class="abs post" style="left:787px">
    <div class="post-img" role="img" aria-label="Skincare portrait on a warm taupe background" style="background:radial-gradient(ellipse 70px 100px at 180px 110px,#ecd2bf 0%,rgba(236,210,191,0) 100%),radial-gradient(ellipse 90px 70px at 170px 20px,#3e2b22 0%,rgba(62,43,34,0) 100%),linear-gradient(135deg,#ae8e73,#d6bfa8)"></div>
    <h3 class="post-title">SED UT PERSPICIATIS UNDE</h3>
    <div class="post-date"><svg width="14" height="14" viewBox="0 0 14 14"><rect x="1" y="2.5" width="12" height="10.5" fill="none" stroke="#c8952a" stroke-width="1.4"/><line x1="1" y1="5.5" x2="13" y2="5.5" stroke="#c8952a" stroke-width="1.4"/></svg>02 Aug 2018</div>
    <p class="post-text">Nemo enim ipsam voluptatem quia voluptas sit aspernatur aut odit aut fugit, sed quia consequuntur magni dolores eos qui ratione voluptatem sequi nesciunt.</p>
  </article>
</section>

<footer class="site-footer">
  <div class="abs f-col" style="left:94px">
    <div class="f-head">PAYMENTS ACCEPTED</div>
    <div class="cards"><div class="card">Payra</div><div class="card">Cirqa</div><div class="card">Amvero</div><div class="card">Findly</div></div>
    <div class="socials"><div class="social">Folio</div><div class="social">Chirpa</div><div class="social">Pictoval</div><div class="social">Linkra</div><div class="social">Vidora</div></div>
  </div>
  <div class="abs f-col" style="left:344px">
    <div class="f-head">INFORMATION</div>
    <ul class="f-list"><li>Sed ut perspiciatis</li><li>unde omnis iste</li><li>natus error sit</li><li>voluptatem accusantium</li><li>doloremque laudantium</li></ul>
  </div>
  <div class="abs f-col" style="left:559px">
    <div class="f-head">CUSTOMER SERVICE</div>
    <ul class="f-list"><li>Sed ut perspiciatis</li><li>unde omnis iste</li><li>natus error sit</li><li>voluptatem accusantium</li><li>doloremque laudantium</li></ul>
  </div>
  <div class="abs f-col" style="left:780px">
    <div class="f-head">MY ACCOUNT</div>
    <ul class="f-list"><li>My account</li><li>Orders</li><li>Addresses</li><li>Shopping cart</li><li>Wishlist</li></ul>
  </div>
  <div class="abs f-col" style="left:936px">
    <div class="f-head">CONTACT US</div>
    <div class="contact-row"><svg width="13" height="13" viewBox="0 0 13 13"><rect x="1" y="1" width="11" height="11" rx="2" fill="#ddd"/><path d="M4 3.5l1.5 1.5-1 1c.6 1.1 1.4 1.9 2.5 2.5l1-1L9.5 9 8.5 10C6 9.5 3.5 7 3 4.5z" fill="#000"/></svg><span>(000)-121-1231 (Phone)</span></div>
    <div class="contact-row"><svg width="13" height="13" viewBox="0 0 13 13"><rect x="3" y="1" width="7" height="4" fill="#ddd"/><rect x="1" y="5" width="11" height="5" fill="#ddd"/><rect x="3" y="9" width="7" height="3" fill="#ddd"/></svg><span>(000)-121-1231&nbsp;&nbsp;&nbsp;&nbsp;(Fax)</span></div>
    <div class="contact-row"><svg width="13" height="13" viewBox="0 0 13 13"><rect x="1" y="2.5" width="11" height="8" fill="#ddd"/><polyline points="1,2.5 6.5,7 12,2.5" fill="none" stroke="#000" stroke-width="1.2"/></svg><span style="text-decoration:underline">info@corvanthveylor.com</span></div>
    <div class="contact-row"><svg width="13" height="13" viewBox="0 0 13 13"><path d="M6.5 12.5C4 9 2.5 7 2.5 5a4 4 0 018 0c0 2-1.5 4-4 7.5z" fill="#ddd"/><circle cx="6.5" cy="5" r="1.5" fill="#000"/></svg><span>#254 Lorem Ipsum Dummy<br>Text Lorem Ipsum</span></div>
  </div>
  <div class="abs f-rule"></div>
  <p class="abs center copyright">© Copyright 2018 Corvanth Veylor All Rights Reserved</p>
</footer>

</body>
</html>
```